Pinegate Marketing 8 page broshure

I need a design for an 8 page 8.5 X 11 booklet for my company. Our company colors are dark blue, light blue, and white. I am uploading some files for language that you may use. One of the files is our logo. please use the phrase: To us business is a contact sport as well as Pinegate Marketing is your complete marketing solution. Include something about we offer web and brochure design.as well as social media marketing.

Dear Velkan at Artisan Bazaar, Dear Velkan, we just spoke on the phone about my project for Pinegate Marketing Group sales brochure. As we discussed there are several things wrong with the final version that the Tumble sent to me. First of all the design is completely wrong, It is designed to be 8.5 x 11 when it should be designed to be 8.5 X 5.5 and the fold in the booklet should be the 8.5 side. In other words if you take and 8.5 x 11 piece of paper and fold in half that makes a booklet of 8.5 x 5.5. The other problem that were having with this is that there is no page covering our CRM product which is very important to our service offerings. I have sent you files that cover the CRM but for some reason it wasn't put in. Two small changes, on the front cover I see that we have on the very bottom of the of the page there is a line that says as well as Pinegate marketing is your complete marketing solution. I would like that line taken out. On the back cover I would like to change the address at the very bottom of the page the new address will be 41957 Kimber Ave., Westlake, OH 44163 I think if those changes are made we are about ready to go. Don't misunderstand we love your work, you guys have worked hard and the design is very good there just so's changes to make. Thank you very much, Oliver Marsh

Target Market(s)

Any business that needs help with increasing their sales and marketing in their company. We also have a fully customizable CRM so they may track the leads that are in their pipeline as well as those leads we bring in to their pipeline. On the marketing side we offer many services. Two things that I could not download was we do website design srvices and social media marketing.

Industry/Entity Type

It Company

Font styles to use
Sans Serif

Colors
0555a3
00a990
ffffff

Requirements
Must have
• Company logo on front cover, Stress the various services we offer on the marketing side, stress the CRM - very important. Feel free to use any of the dowloads I am sending to you for text.
Nice to have
• Very professional and elegant presentation.
Should not have
• Should not have any drawings or things that look out of place. Stock picture are fine as long as they have something to do with marketing or CRM.

```html
<!DOCTYPE html>
<html lang="en">
<head>
<meta charset="utf-8">
<title>Pinegate Marketing – Brochure Pages 3 &amp; 4</title>
<link href="https://fonts.googleapis.com/css2?family=Roboto+Condensed:ital,wght@0,300;0,400;1,300&display=swap" rel="stylesheet">
<style>
  :root {
    --backdrop-top: #f2f2f2;
    --backdrop-bottom: #c9c9c9;
    --paper: #ffffff;
    --ink: #3a3a3a;
    --accent: #2a6fc1;
    --navy: #0b1f33;
    --steel: #2c5a7a;
    --ice: #a9d4ec;
    --label: #ffffff;
  }
  * { margin: 0; padding: 0; box-sizing: border-box; }
  html, body { width: 1200px; height: 800px; overflow: hidden; }
  body {
    background: radial-gradient(ellipse at 50% 30%, var(--backdrop-top) 0%, var(--backdrop-bottom) 100%);
    font-family: "Roboto Condensed", "Arial Narrow", sans-serif;
    position: relative;
  }
  .spread {
    position: absolute;
    left: 107px; top: 54px;
    width: 987px; height: 648px;
    display: flex;
    box-shadow: 0 6px 22px rgba(0,0,0,0.22);
  }
  .page {
    position: relative;
    width: 493.5px; height: 648px;
    background: var(--paper);
    overflow: hidden;
  }
  .page-heading {
    font-weight: 300;
    font-style: italic;
    color: var(--accent);
    font-size: 25px;
    letter-spacing: -0.3px;
    line-height: 1;
    margin-bottom: 14px;
  }
  .body-copy p {
    font-weight: 300;
    font-size: 9.4px;
    line-height: 12.7px;
    color: var(--ink);
    text-align: justify;
    margin-bottom: 12.5px;
  }
  .slogan { color: var(--accent); }

  .hero-photo { position: absolute; left: 0; top: 0; width: 493.5px; height: 270px; }
  .services { position: absolute; left: 77px; top: 278px; width: 350px; }

  .lead-gen { position: absolute; left: 56px; top: 64px; width: 368px; }
  .desk-photo { position: absolute; left: 0; bottom: 0; width: 493.5px; height: 290px; }

  .page-label {
    position: absolute;
    right: 106px; top: 722px;
    color: var(--label);
    font-weight: 300;
    font-size: 38px;
    letter-spacing: 1px;
  }
</style>
</head>
<body>
  <main class="spread">
    <section class="page page-left">
      <svg class="hero-photo" viewBox="0 0 493.5 270" role="img" aria-label="Photo of a businessman drawing a rising success chart with a world map on a glowing screen">
        <defs>
          <linearGradient id="heroTone" x1="0" y1="0" x2="1" y2="1">
            <stop offset="0" stop-color="#081624"/>
            <stop offset="0.45" stop-color="#2c5a7a"/>
            <stop offset="0.7" stop-color="#7fb6d4"/>
            <stop offset="1" stop-color="#10263a"/>
          </linearGradient>
        </defs>
        <path d="M0 0 H493.5 V265 C430 250 380 225 300 240 C220 255 150 270 80 245 C45 233 20 230 0 240 Z" fill="url(#heroTone)"/>
      </svg>

      <div class="services body-copy">
        <h2 class="page-heading">Services Offered</h2>
        <p>Pinegate Marketing is proud to offer the following services</p>
        <p>We provide the best, most productive, cost effective (ROI) outbound Lead Generation service in the country.</p>
        <p>Pinegate Marketing can offer not only Outbound Lead Generation but there is great success in Inbound Marketing. We will field your inbound calls relating to sales prospects as well as your customer questions and complaints.</p>
        <p>Effective Email Campaigns. This type of marketing can easily be combined with the outbound and inbound strategies.</p>
        <p>Direct Mail. From the database generated specifically for your company we can do a Direct Mail campaign.</p>
        <p>We can provide expert training for Sales Representatives as well as expert training of Outbound and Inbound Representatives. We have been around for over 23 years in this business. We know what works and what doesn't work. Many things go into the training of these employees. There is a big difference between a person who say's they are a salesperson or a telemarketing person and a trained expert trained by us. There are statistics that show a Salesperson can be the best thing your company can do or the worst thing and most expensive employee within your company.</p>
      </div>
    </section>

    <section class="page page-right">
      <div class="lead-gen body-copy">
        <h2 class="page-heading">Business to Business Lead Generation</h2>
        <p>Pinegate Marketing Group has become one of the most influential lead generation companies in the industry, helping thousands of organizations create more sales leads, improve the qualification of their business leads, and boost conversion rates throughout the sales process. If you need more sales leads, or need to make better use of the business leads that you have, talk to our team and see how we can improve your B2B lead generation effort.</p>
        <p>Learn why thousands of businesses have chosen Pinegate Marketing Group to be their trusted lead generation partner. Our talented appointment setters and experienced sales agents offer a comprehensive array of lead generation services, making us an industry standard bearer among lead generation companies.</p>
        <p>It is our experience, after having been in this business since 1998, that Sales People do a very poor job of finding new leads for your company. They do not like to cold call for leads and in most cases they either don't do it at all or do a very poor job when making such contact with prospective customers.</p>
        <p>There are several companies out there that will tell you that Outbound Lead Generation is "old school" and that there are many methods out there to obtaining quality leads. We agree that there are other methods of lead generation out there but nothing replaces the "old school" method of B2B Outbound Lead Generation. This is why we continue to believe: <span class="slogan">"To Us Business is a Contact Sport"</span></p>
      </div>

      <svg class="desk-photo" viewBox="0 0 493.5 290" role="img" aria-label="Photo of glasses, a pen and printed sales charts on a reflective blue desk">
        <defs>
          <linearGradient id="deskFade" x1="0" y1="0" x2="0" y2="1">
            <stop offset="0" stop-color="#ffffff"/>
            <stop offset="0.3" stop-color="#dbeaf4"/>
            <stop offset="0.7" stop-color="#8fbfdc"/>
            <stop offset="1" stop-color="#5f9cc4"/>
          </linearGradient>
        </defs>
        <rect width="493.5" height="290" fill="url(#deskFade)"/>
      </svg>
    </section>
  </main>

  <div class="page-label">Page 3 &amp; 4</div>
</body>
</html>
```